TLK Electricial Contracting Services

Hi guys, after a design for my small electrical company, have logo design files to be incorporated into the layout, the basic concept is electrical contracting services for residential, commercial, industrial & data services, image is clean clear and strong,

Card format is to have a nice clean logo on front,with maybe the Residential – commercial – industrial - data, followed with licensed & insured, followed by contact details on backside of the card.

Target Market(s)

Residential, commercial, industrial sectors.

Industry/Entity Type

Electrical

Contact Information for Business Card

TLK logo,
Residential – commercial – industrial - data
REC: 61307
Email: tlk@vornamail.net.au
Phone: 0487 352 019

Requirements
Must have
• Clean & strong design.
Nice to have
• If possible, I would like the logo colours inverted so the text is orange and the background is black on the front of the card, then the backside of the card be the reverse colour
Should not have
• No Sparks, lightning bolts,

```html
<!DOCTYPE html>
<html lang="en">
<head>
<meta charset="utf-8">
<title>TLK Electrical Contracting Services – Business Card</title>
<link href="https://fonts.googleapis.com/css2?family=Michroma&family=Exo+2:ital,wght@1,300&family=Saira:wght@500&display=swap" rel="stylesheet">
<style>
  :root {
    --orange: #f47b20;
    --orange-light: #f8984a;
    --black: #0a0a0a;
    --stage: #ececec;
  }
  * { margin: 0; padding: 0; box-sizing: border-box; }
  html, body { width: 1200px; height: 521px; overflow: hidden; background: var(--stage); }
  .canvas { position: relative; width: 1200px; height: 521px; }

  .card { position: absolute; top: 112px; height: 296px; overflow: hidden; }

  /* Front */
  .card--front { left: 57px; width: 519px; background: var(--black); color: var(--orange); text-align: center; }
  .front__mark {
    position: absolute; top: 58px; left: 0; width: 100%;
    font-family: "Michroma", sans-serif; font-size: 62px; line-height: 1; letter-spacing: 2px;
  }
  .front__name {
    position: absolute; top: 158px; left: 0; width: 100%;
    font-family: "Michroma", sans-serif; font-size: 15px; letter-spacing: .5px;
  }
  .front__tagline {
    position: absolute; top: 203px; left: 40px; right: 40px;
    font-family: "Exo 2", sans-serif; font-style: italic; font-weight: 300;
    font-size: 15px; line-height: 21px; letter-spacing: .5px;
  }

  /* Back */
  .card--back { left: 625px; width: 527px; background: var(--orange); color: var(--black); }
  .back__pattern { position: absolute; left: 200px; top: 40px; width: 327px; height: 230px; }
  .back__band { position: absolute; left: 0; bottom: 0; width: 527px; height: 18px; }
  .back__mark {
    position: absolute; top: 26px; left: 16px;
    font-family: "Michroma", sans-serif; font-size: 44px; line-height: 1; letter-spacing: 1px;
  }
  .back__name {
    position: absolute; top: 96px; left: 34px;
    font-family: "Michroma", sans-serif; font-size: 11.5px;
  }
  .sectors {
    position: absolute; top: 22px; left: 351px; list-style: none;
    font-family: "Saira", sans-serif; font-weight: 500; font-size: 16px; line-height: 21.5px; letter-spacing: .6px;
  }
  .sectors li::before {
    content: ""; display: inline-block; width: 6px; height: 6px; background: var(--black);
    margin-right: 7px; vertical-align: 3px;
  }
  .licence {
    position: absolute; top: 116px; left: 351px;
    font-family: "Exo 2", sans-serif; font-style: italic; font-weight: 300; font-size: 15.5px; letter-spacing: .5px;
  }
  .contact {
    position: absolute; top: 200px; left: 34px;
    font-family: "Saira", sans-serif; font-weight: 500; font-size: 16.5px; line-height: 23px; letter-spacing: .6px;
  }
</style>
</head>
<body>
<main class="canvas">
  <section class="card card--front">
    <div class="front__mark">TLK</div>
    <div class="front__name">Tate Lewis Kirby Electrical</div>
    <p class="front__tagline">Electrical contracting services for residential, commercial, industrial &amp; data services.</p>
  </section>

  <section class="card card--back">
    <svg class="back__pattern" role="img" aria-label="Fine circuit-trace line pattern in light orange" viewBox="0 0 327 230" preserveAspectRatio="none">
      <defs>
        <linearGradient id="traceGlow" x1="0" y1="0" x2="1" y2="1">
          <stop offset="0" stop-color="#f47b20" stop-opacity="0"/>
          <stop offset="1" stop-color="#f8984a" stop-opacity=".8"/>
        </linearGradient>
      </defs>
      <rect width="327" height="230" fill="url(#traceGlow)"/>
    </svg>
    <svg class="back__band" viewBox="0 0 527 18" preserveAspectRatio="none" aria-hidden="true">
      <polygon points="40,0 527,0 527,18 0,18" fill="#0a0a0a"/>
    </svg>

    <div class="back__mark">TLK</div>
    <div class="back__name">Tate Lewis Kirby Electrical</div>

    <ul class="sectors">
      <li>RESIDENTIAL</li>
      <li>COMMERCIAL</li>
      <li>INDUSTRIAL</li>
      <li>DATA</li>
    </ul>
    <div class="licence">REC: 61307</div>

    <div class="contact">
      <div>E-MAIL:&nbsp; TLK@VORNAMAIL.NET.AU</div>
      <div>PHONE: 0487.352.019</div>
    </div>
  </section>
</main>
</body>
</html>
```